Birchline Septic Solutions

Would like to see some single sided ones but would also like to see some double sided with one sided only being the logo. Owners name is Colin Vandro. Phone number is 555-214-0387
Services are pumping, inspections, installs, and repairs

Contact Information for Business Card

555-241-0387 Colin Vandro Alder Falls, OH

```html
<!DOCTYPE html>
<html lang="en">
<head>
<meta charset="utf-8">
<title>Birchline Septic Solutions – Business Cards</title>
<link rel="stylesheet" href="https://fonts.googleapis.com/css2?family=Lato:wght@400;700;900&display=swap">
<style>
  :root {
    --stage: #2b2b2b;
    --card-dark: #050505;
    --card-light: #ffffff;
    --ink: #111111;
    --teal: #2bbcb6;
    --silver: #e4e4e4;
    --muted: #3a3a3a;
  }
  * { box-sizing: border-box; margin: 0; padding: 0; }
  html, body {
    width: 1200px; height: 875px; overflow: hidden;
    background: var(--stage);
    font-family: "Lato", sans-serif;
  }
  .stage {
    position: relative; width: 1200px; height: 875px;
    display: flex; align-items: center; justify-content: center; gap: 48px;
  }
  .card {
    position: relative; width: 540px; height: 309px;
    border-radius: 18px; overflow: hidden;
    box-shadow: 0 18px 40px rgba(0,0,0,.45);
  }
  /* Front: logo side */
  .card--front {
    background: var(--card-dark);
    display: flex; flex-direction: column; align-items: center; justify-content: center;
  }
  .brand-name {
    display: flex; align-items: center; gap: 12px;
    font-weight: 900; letter-spacing: .04em; text-transform: uppercase;
  }
  .brand-name__dot { width: 16px; height: 16px; border-radius: 50%; background: var(--teal); flex: none; }
  .card--front .brand-name { color: var(--silver); font-size: 34px; }
  .tagline {
    margin-top: 26px; color: #ffffff; font-size: 15px; font-weight: 400; letter-spacing: .02em;
  }
  /* Back: contact side */
  .card--back { background: var(--card-light); }
  .card--back .brand-name {
    position: absolute; left: 40px; top: 112px;
    color: var(--ink); font-size: 22px; line-height: 1.15; width: 230px;
  }
  .name-band {
    position: absolute; right: 0; top: 86px; width: 250px; height: 84px;
    background: var(--teal);
    clip-path: polygon(14% 0, 100% 0, 100% 100%, 0 100%);
    display: flex; align-items: center; justify-content: center; padding-left: 26px;
  }
  .owner-name {
    color: var(--ink); font-size: 27px; font-weight: 900; letter-spacing: .01em; text-transform: uppercase;
  }
  .contact-list {
    position: absolute; left: 120px; top: 196px; list-style: none;
  }
  .contact-item { display: flex; align-items: center; gap: 10px; color: var(--ink); }
  .contact-item svg { flex: none; }
  .contact-item--phone { font-size: 22px; font-weight: 700; }
  .contact-item--place { font-size: 18px; font-weight: 400; color: var(--muted); margin-top: 6px; margin-left: 4px; }
  .edge-tab {
    position: absolute; left: 0; bottom: 26px; width: 12px; height: 44px; background: var(--card-dark);
  }
</style>
</head>
<body>
<main class="stage">
  <section class="card card--front" aria-label="Card front">
    <div class="brand-name"><span class="brand-name__dot"></span>Birchline Septic Solutions</div>
    <p class="tagline">Pumping, Inspections, Installs &amp; Repairs</p>
  </section>

  <section class="card card--back" aria-label="Card back">
    <div class="brand-name"><span class="brand-name__dot"></span>Birchline Septic Solutions</div>
    <div class="name-band"><span class="owner-name">Colin Vandro</span></div>
    <ul class="contact-list">
      <li class="contact-item contact-item--phone">
        <svg width="20" height="20" viewBox="0 0 24 24" aria-hidden="true"><path fill="var(--teal)" d="M6.6 10.8a15 15 0 0 0 6.6 6.6l2.2-2.2c.3-.3.7-.4 1-.2 1.1.4 2.3.6 3.6.6.6 0 1 .4 1 1V20c0 .6-.4 1-1 1A17 17 0 0 1 3 4c0-.6.4-1 1-1h3.5c.6 0 1 .4 1 1 0 1.3.2 2.5.6 3.6.1.3 0 .7-.2 1z"/></svg>
        555-241-0387
      </li>
      <li class="contact-item contact-item--place">
        <svg width="16" height="20" viewBox="0 0 16 22" aria-hidden="true"><path fill="var(--teal)" d="M8 0a8 8 0 0 0-8 8c0 6 8 14 8 14s8-8 8-14a8 8 0 0 0-8-8zm0 11a3 3 0 1 1 0-6 3 3 0 0 1 0 6z"/></svg>
        Alder Falls, OH
      </li>
    </ul>
    <div class="edge-tab"></div>
  </section>
</main>
</body>
</html>
```